Card Design for my dog training business Brightpaw Obedience

Need a business card design for my dog training business with my new logo. Want the card to come off professional yet fun. Want it to be very eye catchy as well. I normally have these at vet clinics, pet stores, and groomers. so need it to look better than my competitors.
Target Market(s)
dog owners
Industry/Entity Type
Dog Training
Contact Information for Business Card
needs logo, my name and info
Font styles to use
Serif
Colors
0255a3
ffffff
ec1f27
000000
333333
fbfbfb
Requirements
Must have
- Brightpaw Obedience
- Felix Orland
- 415 903 2276
- info@brightpawobedience.example
- www.brightpawobedience.example

```html
<!DOCTYPE html>
<html lang="en">
<head>
<meta charset="utf-8">
<title>Brightpaw Obedience – Business Card</title>
<link rel="stylesheet" href="https://fonts.googleapis.com/css2?family=Cinzel:wght@400;500&family=EB+Garamond:ital@1&display=swap">
<style>
  :root {
    --page: #fbfbfb;
    --card-light: #ffffff;
    --card-dark: #231f20;
    --ink: #1a1a1a;
    --ink-soft: #333333;
    --paper: #ffffff;
    --art-light-a: #ececec;
    --art-light-b: #cfcfcf;
    --art-dark-a: #3b3738;
    --art-dark-b: #57534f;
  }
  * { box-sizing: border-box; margin: 0; padding: 0; }
  html, body { width: 1125px; height: 1200px; overflow: hidden; }
  body {
    background: var(--page);
    position: relative;
    font-family: "Cinzel", serif;
  }
  .card {
    position: absolute;
    left: 150px;
    width: 826px;
    height: 472px;
    display: flex;
    flex-direction: column;
    align-items: center;
  }
  .card--front { top: 106px; background: var(--card-light); color: var(--ink); border: 1px solid #e4e4e4; }
  .card--back  { top: 639px; background: var(--card-dark); color: var(--paper); }

  .artwork { border-radius: 6px; }
  .card--front .artwork {
    margin-top: 43px;
    width: 312px;
    height: 212px;
    background: linear-gradient(160deg, var(--art-light-a), var(--art-light-b));
  }
  .card--front .artwork-rule {
    width: 202px; height: 3px; background: var(--ink); margin-top: 4px;
  }

  .holder {
    font-size: 31px;
    font-weight: 500;
    letter-spacing: 1px;
    line-height: 1;
    margin-top: 10px;
    padding: 0 8px 10px;
    border-bottom: 2px solid var(--ink);
  }
  .contact {
    margin-top: 6px;
    text-align: center;
    color: var(--ink-soft);
    line-height: 27px;
  }
  .contact__phone { font-size: 21px; letter-spacing: 0.5px; }
  .contact__email { font-size: 15px; letter-spacing: 1px; }
  .web {
    margin-top: 10px;
    padding: 9px 10px 7px;
    border-top: 2px solid var(--ink);
    border-bottom: 2px solid var(--ink);
    font-size: 15px;
    letter-spacing: 1px;
    color: var(--ink-soft);
  }

  .card--back .artwork {
    margin-top: 106px;
    width: 262px;
    height: 172px;
    background: linear-gradient(160deg, var(--art-dark-a), var(--art-dark-b));
  }
  .brand {
    margin-top: 8px;
    padding: 8px 6px 6px;
    border-top: 2px solid var(--paper);
    border-bottom: 2px solid var(--paper);
    font-size: 24px;
    font-weight: 400;
    letter-spacing: 1.5px;
    line-height: 1.1;
  }
  .tagline {
    position: absolute;
    top: 404px;
    width: 100%;
    text-align: center;
    font-family: "EB Garamond", serif;
    font-style: italic;
    font-size: 23px;
  }
</style>
</head>
<body>
  <section class="card card--front">
    <div class="artwork" role="img" aria-label="Illustration of two dogs within a state outline"></div>
    <span class="artwork-rule"></span>
    <h1 class="holder">Felix Orland</h1>
    <div class="contact">
      <p class="contact__phone">P.415 903 2276</p>
      <p class="contact__email">info@brightpawobedience.example</p>
    </div>
    <p class="web">www.brightpawobedience.example</p>
  </section>

  <section class="card card--back">
    <div class="artwork" role="img" aria-label="Illustration of two dogs within a state outline"></div>
    <p class="brand">Brightpaw Obedience</p>
    <p class="tagline">“Training dogs across the city one dog at a time.”</p>
  </section>
</body>
</html>
```